i would like a business card to leave with customers and potential customers for electrical work and for the supply and install of reverse cycle airconditioning in the domestic and commercial market.
I own my own business and im a sole trader. I have an a'class electrical lisence and also a refrigeration lisence so i am
able to offer complete installations in airconditioning by a fully qualified and lisenced tradesman.
im looking for something that comes across as unique and professional.
i had the coluor black and some gold in mind but open to any coluors.
something like Lanterra Electrical & Refrigeration
or Lanterra Air.
i will use this design on a business card to advertise through summer to help generate installs through the busy season.

Target Market(s)

Mainly domestic house holds through summer who are in need of airconditioning and reliable information to acomadate thier cooling and heating requirements

Industry/Entity Type

Electrical

Requirements
Must have
• Business name- Lanterra
My name- Mark Delford
My mobile no- 0438 517 290
My email- mrdelford@qelvo.com.au
Installation & Decomissioning of aiconditioning split systems
LIC NO: TRK 540316
Nice to have
• Lanterra Electrical & Refrigeration

```html
<!DOCTYPE html>
<html lang="en">
<head>
<meta charset="utf-8">
<title>Lanterra Electrical &amp; Refrigeration – Business Card</title>
<link rel="stylesheet" href="https://fonts.googleapis.com/css2?family=PT+Sans:wght@400;700&display=swap">
<style>
  :root {
    --backdrop: #1d1e20;
    --card-dark: #2f383c;
    --card-mid: #4c585c;
    --card-light: #8c9ca0;
    --sheen: #c9d6d8;
    --ink: #ffffff;
    --ink-soft: #b9c2c4;
    --flourish-dark: rgba(24, 28, 30, 0.95);
    --flourish-mid: rgba(40, 48, 52, 0.55);
    --shadow: rgba(0, 0, 0, 0.85);
  }
  * { margin: 0; padding: 0; box-sizing: border-box; }
  html, body {
    width: 1200px;
    height: 1198px;
    overflow: hidden;
    background: var(--backdrop);
    font-family: "PT Sans", Arial, sans-serif;
    color: var(--ink);
  }
  .canvas { position: relative; width: 1200px; height: 1198px; }

  .card {
    position: absolute;
    overflow: hidden;
    box-shadow: 14px 14px 0 var(--shadow);
  }
  .card--front {
    left: 79px; top: 135px; width: 705px; height: 440px;
    background: linear-gradient(205deg, var(--sheen) 0%, var(--card-light) 14%, var(--card-mid) 42%, var(--card-dark) 80%);
  }
  .card--back {
    left: 408px; top: 612px; width: 710px; height: 444px;
    background: linear-gradient(150deg, var(--sheen) 0%, var(--card-light) 14%, var(--card-mid) 42%, var(--card-dark) 82%);
  }

  .flourish { position: absolute; inset: 0; pointer-events: none; }
  .card--front .flourish {
    background: radial-gradient(ellipse 250px 150px at 70% 0%, var(--flourish-dark) 0%, var(--flourish-mid) 55%, rgba(40, 48, 52, 0) 100%);
  }
  .card--back .flourish {
    background: radial-gradient(ellipse 230px 140px at 16% 0%, var(--flourish-dark) 0%, var(--flourish-mid) 55%, rgba(40, 48, 52, 0) 100%);
  }

  .rule {
    position: absolute;
    height: 4px;
    border-radius: 2px;
    background: linear-gradient(90deg, rgba(255,255,255,0.95), rgba(255,255,255,0.6) 70%, rgba(255,255,255,0));
  }
  .rule--reverse { background: linear-gradient(90deg, rgba(255,255,255,0), rgba(255,255,255,0.6) 30%, rgba(255,255,255,0.95)); }

  .company-name {
    position: absolute; left: 30px; top: 88px;
    font-size: 26px; font-weight: 700; letter-spacing: 0.2px;
  }
  .person { position: absolute; right: 86px; top: 322px; text-align: right; }
  .person-name { font-size: 34px; font-weight: 700; line-height: 1; }
  .person-role { font-size: 20px; color: var(--ink-soft); line-height: 1.2; }

  .contact-list {
    position: absolute; left: 432px; top: 131px;
    list-style: none; font-size: 21px; line-height: 30px;
  }
  .social-marks { position: absolute; left: 456px; top: 323px; display: flex; gap: 22px; }
  .social-mark { width: 28px; height: 28px; border-radius: 4px; background: var(--ink-soft); opacity: 0.75; }
  .service-note {
    position: absolute; left: 0; width: 516px; top: 376px;
    text-align: center; font-size: 17px; line-height: 22px;
  }
</style>
</head>
<body>
<main class="canvas">
  <section class="card card--front">
    <div class="flourish" role="img" aria-label="Dark sweeping decorative flourish"></div>
    <div class="rule" style="left:0; top:69px; width:470px;"></div>
    <h1 class="company-name">Lanterra Electrical &amp; Refrigeration</h1>
    <div class="rule" style="left:0; top:131px; width:400px;"></div>
    <div class="person">
      <p class="person-name">Mark Delford</p>
      <p class="person-role">CEO</p>
    </div>
  </section>

  <section class="card card--back">
    <div class="flourish" role="img" aria-label="Dark sweeping decorative flourish"></div>
    <div class="rule rule--reverse" style="left:290px; top:99px; width:420px;"></div>
    <ul class="contact-list">
      <li>438 517 290</li>
      <li>mrdelford@qelvo.com.au</li>
      <li>posts.lanterra.au/mark</li>
      <li>pages.lanterra.au/mark</li>
      <li>profile.lanterra.au/mark</li>
    </ul>
    <div class="rule rule--reverse" style="left:258px; top:290px; width:452px;"></div>
    <div class="social-marks">
      <span class="social-mark"></span>
      <span class="social-mark"></span>
      <span class="social-mark"></span>
      <span class="social-mark"></span>
    </div>
    <p class="service-note">Installation &amp; Decomissioning of aiconditioning split systems<br>LIC NO: TRK 540316</p>
  </section>
</main>
</body>
</html>
```